redesign of my existing custom website into Wordpress based website

I need someone to redesign my current website into something more classy, simplistic, modern and on trend. I would like it set up on Wordpress in a way thats easy for me to make my own additions to blogs/price changes and promotion banners. I will also need a page that is password protected so members can login and have access to all my training videos and resources.
website is www.tidewellmamas.com.au

Target Market(s)

new mums

Industry/Entity Type

Fitness

Coding

Coded - Design and coding required

Number of Pages Required

5+ page

Colors
33a6d7

Requirements
Must have
• chic, modern, stylish and simplistic.
• a call to action above the page fold
• mobile friendly conversion
• a pop up message as soon as someone enters my sight offering my free report
• a members page that is password protected containing 3 youtube videos and 6 pdf attachments as resources
• a home page
• a contact us page
• an about us page
• a blog page
• a store page
Nice to have
• some examples of my peers websites that I like:
• www.norapellwick.com
• https://www.9qlr.com
• https://41bytedgarth.com
Should not have
• anything gimmicky

```html
<!DOCTYPE html>
<html lang="en">
<head>
<meta charset="utf-8">
<title>Tidewell Mamas – Home Fitness</title>
<link href="https://fonts.googleapis.com/css2?family=Roboto:ital,wght@0,300;0,400;0,500;0,700;1,400&family=Roboto+Condensed:ital,wght@0,400;0,700;1,700&display=swap" rel="stylesheet">
<style>
:root{
  --pink:#e5147f;
  --pink-dark:#c80f6c;
  --blue:#33a6d7;
  --cyan:#1bb6e8;
  --ink:#2b2b2b;
  --grey:#6d6d6d;
  --light:#f4f4f4;
  --dark:#1f1f1f;
  --darker:#141414;
  --white:#ffffff;
}
*{margin:0;padding:0;box-sizing:border-box}
html,body{width:1200px;height:4027px;overflow:hidden}
body{font-family:'Roboto',sans-serif;color:var(--ink);background:var(--white);position:relative}
.abs{position:absolute}
a{color:inherit;text-decoration:none}

/* header */
.site-header{position:absolute;top:0;left:0;width:1200px;height:129px;background:var(--white);z-index:3}
.brand-badge{position:absolute;left:78px;top:12px;width:182px;height:182px;border-radius:50%;background:var(--white);box-shadow:0 3px 12px rgba(0,0,0,.18);display:flex;flex-direction:column;align-items:center;justify-content:center;z-index:4}
.brand-name{font-family:'Roboto',sans-serif;font-weight:500;font-size:22px;color:var(--pink);line-height:1.15;text-align:center}
.search-box{position:absolute;left:588px;top:27px;width:217px;height:27px;border:1px solid #cfcfcf;border-radius:14px;font-size:11px;color:#999;padding:6px 14px}
.search-box svg{position:absolute;right:10px;top:6px}
.account-links{position:absolute;left:838px;top:33px;font-size:12px;color:#555;display:flex;gap:22px;letter-spacing:.3px}
.account-links span::before{content:"";display:inline-block;width:9px;height:9px;border:1.5px solid #777;border-radius:2px;margin-right:6px;vertical-align:-1px}
.main-nav{position:absolute;top:84px;left:435px;font-size:13px;letter-spacing:.6px;color:#333}
.main-nav span{position:absolute;white-space:nowrap}
.nav-cta{position:absolute;left:961px;top:72px;width:140px;height:38px;background:var(--pink);color:var(--white);font-size:14px;font-weight:500;border-radius:3px;display:flex;align-items:center;justify-content:center}

/* hero */
.hero{position:absolute;top:129px;left:0;width:1200px;height:542px;background:linear-gradient(100deg,#3a3431 0%,#6d5a52 30%,#c5b3a6 55%,#8c7a70 80%,#4b3f3a 100%)}
.hero-title{position:absolute;left:656px;top:356px;width:520px;font-family:'Roboto Condensed',sans-serif;font-style:italic;font-weight:700;font-size:34px;line-height:48px;color:var(--white);text-transform:uppercase;text-shadow:0 2px 6px rgba(0,0,0,.35);white-space:nowrap}
.hero-arrow{position:absolute;top:385px}

/* included */
.section-title{position:absolute;width:1200px;text-align:center;font-size:28px;font-weight:400;color:var(--ink);letter-spacing:.5px;text-transform:uppercase}
.section-sub{position:absolute;width:1200px;text-align:center;font-size:15px;color:#444}
.title-rule{position:absolute;left:560px;width:80px;height:2px;background:var(--cyan)}
.intro{position:absolute;left:101px;top:886px;width:420px;font-size:15px;line-height:1.5;color:#444}
.feature{position:absolute;width:560px}
.feature-icon{position:absolute;left:0;top:0;width:62px;height:62px;border-radius:50%;display:flex;align-items:center;justify-content:center}
.feature-icon.pink{background:var(--pink)}
.feature-icon.cyan{background:var(--cyan)}
.feature h3{margin-left:84px;font-size:15.5px;font-weight:500;color:#222;margin-bottom:8px}
.feature p{margin-left:84px;font-size:12px;line-height:1.65;color:#666;width:460px}
.photo-circle{position:absolute;border-radius:50%}

/* results */
.results{position:absolute;top:1780px;left:0;width:1200px;height:556px;background:linear-gradient(180deg,#1c1c1c,#2c2a29 50%,#1b1b1b)}
.results-title{position:absolute;top:1847px;width:1200px;text-align:center;color:var(--white);font-size:24px;line-height:1.45;text-transform:uppercase;letter-spacing:.4px}
.result-card{position:absolute;top:1955px;width:215px;height:300px;background:var(--white);text-align:center}
.result-photo{height:165px;margin:5px 5px 0}
.result-card h4{font-size:16px;font-weight:400;color:#333;margin-top:14px}
.result-card .role{font-size:11px;color:#777;margin-top:5px}
.result-card .stat{font-size:15px;color:var(--pink);margin-top:12px;line-height:1.35}
.result-card .quote{font-size:11px;color:#666;margin:12px 16px 0;line-height:1.5}
.result-card .sep{width:180px;height:1px;background:#e3e3e3;margin:8px auto 0}

/* why */
.why-card{position:absolute;top:2518px;width:312px}
.why-photo{height:180px}
.why-card h3{font-size:15px;font-weight:500;color:#222;margin-top:22px;text-transform:uppercase}
.why-card p{font-size:12px;line-height:1.6;color:#666;margin-top:8px;width:300px}
.why-card .more{display:block;font-size:13px;color:#222;margin-top:12px;letter-spacing:.4px}

/* cta band */
.cta-band{position:absolute;top:2900px;left:0;width:1200px;height:408px;background:linear-gradient(90deg,#8fd0ec 0%,#5cbde4 40%,#53b7e0 70%,#7ccaea 100%)}
.cta-title{position:absolute;top:3026px;width:1200px;text-align:center;color:var(--white);font-size:32px;font-weight:500;text-transform:uppercase;letter-spacing:.4px}
.cta-sub{position:absolute;top:3075px;width:1200px;text-align:center;color:var(--white);font-size:18px}
.cta-btn{position:absolute;left:505px;top:3120px;width:190px;height:40px;border:2px solid var(--white);color:var(--white);font-size:14px;display:flex;align-items:center;justify-content:center;letter-spacing:.6px}

/* testimonials */
.testimonial-text{position:absolute;left:170px;top:3443px;width:860px;text-align:center;font-style:italic;font-size:13px;line-height:1.75;color:#777}
.testimonial-name{position:absolute;top:3537px;width:1200px;text-align:center;font-size:17px;color:#444}
.testimonial-name em{color:var(--pink);font-weight:500}

/* footer */
.footer{position:absolute;top:3652px;left:0;width:1200px;height:316px;background:var(--dark)}
.footer-avatar{position:absolute;left:539px;top:3583px;width:120px;height:120px;border-radius:50%;border:4px solid var(--white);background:radial-gradient(circle at 50% 40%,#b89584,#5a4a42);z-index:2}
.footer-heading{position:absolute;top:3735px;color:var(--white);font-size:14px;font-weight:500;letter-spacing:.6px;text-transform:uppercase}
.footer-brand{position:absolute;left:95px;top:3745px;color:var(--white);font-size:24px;font-weight:500;line-height:1.2;text-align:center;width:170px}
.news-copy{position:absolute;left:341px;top:3772px;width:270px;font-size:11.5px;line-height:1.55;color:#ccc}
.news-form{position:absolute;left:341px;top:3822px;display:flex}
.news-form .field{width:190px;height:38px;background:var(--white);font-size:11px;color:#999;padding:12px 10px}
.news-form .send{width:78px;height:38px;background:var(--cyan);color:var(--white);font-size:11px;display:flex;align-items:center;justify-content:center}
.social{position:absolute;left:341px;top:3882px;display:flex;gap:8px}
.social i{width:22px;height:22px;border-radius:50%;background:var(--white);display:block}
.tweet{position:absolute;left:682px;width:230px;font-size:11px;line-height:1.5;color:#ccc}
.tweet::before{content:"";position:absolute;left:0;top:2px;width:16px;height:16px;background:var(--white);border-radius:2px}
.tweet p{margin-left:28px}
.tweet b{color:var(--cyan);font-weight:400}
.tweet small{display:block;margin-left:28px;color:#999;font-size:10.5px;margin-top:4px}
.quick-links{position:absolute;left:996px;top:3772px;font-size:12px;line-height:2.05;color:#ddd;list-style:none}
.copyright{position:absolute;top:3968px;left:0;width:1200px;height:59px;background:var(--darker);color:#ccc;font-size:12px;display:flex;align-items:center;justify-content:center}
</style>
</head>
<body>

<header class="site-header">
  <div class="search-box">Search here
    <svg width="14" height="14" viewBox="0 0 14 14"><circle cx="6" cy="6" r="4.5" fill="none" stroke="#888" stroke-width="1.5"/><line x1="9.5" y1="9.5" x2="13" y2="13" stroke="#888" stroke-width="1.5"/></svg>
  </div>
  <div class="account-links"><span>REGISTER</span><span>LOGIN</span><span>MY ACCOUNT</span></div>
  <nav class="main-nav">
    <span style="left:0">HOME</span>
    <span style="left:72px">ABOUT US</span>
    <span style="left:172px">PROGRAM</span>
    <span style="left:271px">BLOG</span>
    <span style="left:341px">SHOP</span>
    <span style="left:413px">CONTACT US</span>
  </nav>
  <a class="nav-cta">Get It FREE Now!</a>
</header>

<div class="brand-badge"><span class="brand-name">Tidewell<br>Mamas</span></div>

<section class="hero" role="img" aria-label="Photo of a mother exercising on a step in a living room with her baby beside her">
  <svg class="hero-arrow" style="left:26px" width="22" height="38" viewBox="0 0 22 38"><polyline points="18,3 4,19 18,35" fill="none" stroke="rgba(255,255,255,.8)" stroke-width="3"/></svg>
  <svg class="hero-arrow" style="left:1152px" width="22" height="38" viewBox="0 0 22 38"><polyline points="4,3 18,19 4,35" fill="none" stroke="rgba(255,255,255,.8)" stroke-width="3"/></svg>
</section>
<h1 class="hero-title">Lose your baby weight &amp; bounce<br>back into shape! 12 week home<br>workout program for mums!</h1>

<h2 class="section-title" style="top:742px">What's included in the program?</h2>
<p class="section-sub" style="top:788px">12 week Home Workout Program - Equipment Pack</p>
<div class="title-rule" style="top:830px"></div>

<p class="intro">Your purchase of the Home Workout Program -<br>Equipment Pack comes loaded with value including:</p>

<div class="feature" style="left:101px;top:964px">
  <div class="feature-icon pink"><svg width="32" height="24" viewBox="0 0 32 24"><circle cx="7" cy="18" r="5" fill="none" stroke="#fff" stroke-width="2.5"/><circle cx="25" cy="18" r="5" fill="none" stroke="#fff" stroke-width="2.5"/><polyline points="7,18 13,6 21,6 25,18" fill="none" stroke="#fff" stroke-width="2.5"/></svg></div>
  <h3>Our unique 3 stage, 12 week training program</h3>
  <p>Gradually build back your fitness and core strength and also lose baby weight with our training circuit and fitness program. We take you through 6 workout programs that increase with intensity and are designed for new mums as well as experienced mums.</p>
</div>
<div class="feature" style="left:101px;top:1079px">
  <div class="feature-icon pink"><svg width="28" height="28" viewBox="0 0 28 28"><circle cx="14" cy="14" r="12" fill="none" stroke="#fff" stroke-width="2.5"/><circle cx="14" cy="14" r="3" fill="#fff"/></svg></div>
  <h3>Full Instructional Workout DVD and program cards for each program</h3>
  <p>You can either do your home workout along with us on DVD, or use your program cards and do it yourself while hanging with your family watching your favourite tv shows.</p>
</div>
<div class="feature" style="left:101px;top:1172px">
  <div class="feature-icon pink"><svg width="24" height="28" viewBox="0 0 24 28"><rect x="2" y="3" width="20" height="23" rx="2" fill="none" stroke="#fff" stroke-width="2.5"/><polyline points="7,14 11,18 17,10" fill="none" stroke="#fff" stroke-width="2.5"/></svg></div>
  <h3>Weekly accountability charts</h3>
  <p>Keep yourself accountable with our tick charts that let you tick off each time you workout so you can keep track of what your doing to ensure your always on top of it!</p>
</div>

<div class="photo-circle" style="left:736px;top:830px;width:300px;height:300px;background:var(--pink)"></div>
<div class="photo-circle" style="left:751px;top:845px;width:270px;height:270px;background:radial-gradient(circle at 50% 40%,#d8b5a2,#8a6a5c 70%,#6c4f45)" role="img" aria-label="Portrait of the program founder in a green workout top"></div>

<div class="photo-circle" style="left:93px;top:1340px;width:350px;height:350px;background:var(--cyan)"></div>
<div class="photo-circle" style="left:128px;top:1375px;width:280px;height:280px;background:linear-gradient(135deg,#d5c9d6,#a77fa8 45%,#e8dde6)" role="img" aria-label="Equipment pack with DVD, program cards and exercise step"></div>

<div class="feature" style="left:537px;top:1368px">
  <div class="feature-icon cyan"><svg width="28" height="20" viewBox="0 0 28 20"><rect x="2" y="2" width="24" height="16" rx="2" fill="none" stroke="#fff" stroke-width="2.5"/><polyline points="2,3 14,12 26,3" fill="none" stroke="#fff" stroke-width="2.5"/></svg></div>
  <h3>Weekly coaching emails</h3>
  <p>Stay focused and motivated with our weekly emails that give more information on what to do each week and tips to keep you on track.</p>
</div>
<div class="feature" style="left:537px;top:1462px">
  <div class="feature-icon cyan"><svg width="32" height="16" viewBox="0 0 32 16"><rect x="1" y="3" width="5" height="10" fill="#fff"/><rect x="26" y="3" width="5" height="10" fill="#fff"/><rect x="6" y="6" width="20" height="4" fill="#fff"/></svg></div>
  <h3>Funky exercise equipment for your home</h3>
  <p>We bring you all the tools you need to be able to do this workout from home. You no longer need to hide away those ugly dumbbells, our cool equipment is designed to be out on display, keeping you motivated all the time.</p>
</div>
<div class="feature" style="left:537px;top:1575px">
  <div class="feature-icon cyan"><svg width="24" height="26" viewBox="0 0 24 26"><circle cx="12" cy="15" r="9" fill="none" stroke="#fff" stroke-width="2.5"/><line x1="12" y1="6" x2="14" y2="1" stroke="#fff" stroke-width="2.5"/></svg></div>
  <h3>Nutritionist approved healthy eating guide</h3>
  <p>Leading nutritionist Maren Colby, provides her expert advice on how to eat a healthy balanced diet that will compliment your training and assist your weight loss goals.</p>
</div>

<section class="results"></section>
<h2 class="results-title">Check out some of the awesome results already<br>achieved by mums on our program</h2>

<article class="result-card" style="left:102px">
  <div class="result-photo" style="background:linear-gradient(90deg,#8fb8cf,#c9a58e 50%,#9fc2d2)" role="img" aria-label="Before and after photos of a mum at the beach"></div>
  <h4>Delphine</h4><p class="role">Tidewell Mamas Founder</p><div class="sep"></div>
  <p class="stat">Lost 12 kgs and 25 cms<br>in 12 weeks!</p>
</article>
<article class="result-card" style="left:357px">
  <div class="result-photo" style="background:linear-gradient(90deg,#c79c92,#e3c6c6 50%,#a9c29a)" role="img" aria-label="Before and after photos of a mum in workout clothes"></div>
  <h4>Marisa</h4><p class="role">Mum of Two, Keen Runner</p><div class="sep"></div>
  <p class="stat">Lost 20 cms in<br>12 weeks!</p>
</article>
<article class="result-card" style="left:615px">
  <div class="result-photo" style="background:linear-gradient(180deg,#e0d4cf,#b58a78)" role="img" aria-label="Photo of a mum in a sports top after the program"></div>
  <h4>KL</h4><p class="role">Lost 18cms in 8 weeks!</p><div class="sep"></div>
  <p class="quote">This program was exactly what I needed to help get back into shape</p>
</article>
<article class="result-card" style="left:867px">
  <div class="result-photo" style="background:linear-gradient(180deg,#f3d9a6,#e0a55a 60%,#9c6a3c)" role="img" aria-label="Silhouette of a mum stretching at sunset"></div>
  <h4>Ivy</h4><p class="role">Lost 31 cms and 10kgs in 8 weeks!</p><div class="sep"></div>
  <p class="quote">This was a great program for me as it fitted in so well with my busy life</p>
</article>

<h2 class="section-title" style="top:2405px">Why our program is different</h2>
<div class="title-rule" style="top:2459px"></div>

<article class="why-card" style="left:99px">
  <div class="why-photo" style="background:linear-gradient(120deg,#7a6a62,#b79f92 50%,#5a4b45)" role="img" aria-label="Mum doing a plank at home next to her baby"></div>
  <h3>Specially designed for mums</h3>
  <p>Unlike other home workout programs out there ours is designed specially for mums. Because our bodies go through such a major change during pregnancy.</p>
  <a class="more">LEARN MORE &#9656;</a>
</article>
<article class="why-card" style="left:443px">
  <div class="why-photo" style="background:linear-gradient(120deg,#6e5f58,#a58f86 50%,#4e6f7b)" role="img" aria-label="Baby playing with colourful exercise steps"></div>
  <h3>Workout equipment included ..</h3>
  <p>Unlike other home workout programs out there ours is designed specially for mums. Because our bodies go through such a major change during pregnancy.</p>
  <a class="more">LEARN MORE &#9656;</a>
</article>
<article class="why-card" style="left:787px">
  <div class="why-photo" style="background:linear-gradient(120deg,#c9b59a,#b4472e 45%,#6d8d3f 75%,#d9cbb2)" role="img" aria-label="Bowl of a healthy low fat salad"></div>
  <h3>Delicious low fat family friendly</h3>
  <p>Diet meal planners with shopping lists and strict daily instructions on what to eat are not always convenient when you have a whole family to please.</p>
  <a class="more">LEARN MORE &#9656;</a>
</article>

<section class="cta-band" role="img" aria-label="Faded photo of a smiling mum and baby exercising on the floor"></section>
<h2 class="cta-title">Take the first step today by joining our program</h2>
<p class="cta-sub">and let us help you bounce back to the body that you deserve!</p>
<a class="cta-btn">GET STARTED NOW!</a>

<h2 class="section-title" style="top:3377px">Testimonials</h2>
<p class="testimonial-text">“ Having a newborn left me tired and out of shape, but these short home sessions fitted perfectly around naps and feeds. The plan is easy to follow, the coaching emails kept me going and the recipes are a hit with the whole family. I feel stronger than ever and finally like myself again. ”</p>
<p class="testimonial-name"><em>John Doe</em> - Tidewell Mamas</p>

<footer class="footer"></footer>
<svg class="abs" style="left:0;top:3600px" width="1200" height="60" viewBox="0 0 1200 60"><path d="M0 52 Q600 -20 1200 52 L1200 60 L0 60 Z" fill="#1f1f1f"/></svg>
<div class="footer-avatar" role="img" aria-label="Small portrait of the program founder"></div>

<div class="footer-brand">Tidewell<br>Mamas</div>
<h5 class="footer-heading" style="left:341px">Join our newsletter</h5>
<p class="news-copy">Sign up for weekly tips, new recipes and early news on our latest programs.</p>
<div class="news-form"><span class="field">Enter Name</span><span class="send">SUBSCRIBE</span></div>
<div class="social"><i></i><i></i><i></i><i></i></div>

<h5 class="footer-heading" style="left:682px">Latest tweet`s</h5>
<div class="tweet" style="top:3772px"><p><b>@Tidewell Mamas</b> New recipe just added to the members area</p><small>1 day ago</small></div>
<div class="tweet" style="top:3840px"><p><b>@Tidewell Mamas</b> Week two challenge starts on Monday mums</p><small>1 day ago</small></div>

<h5 class="footer-heading" style="left:996px">Quick links</h5>
<ul class="quick-links"><li>Home</li><li>About Us</li><li>Programs</li><li>Blog</li><li>Shop</li><li>Contact</li></ul>

<div class="copyright">Copyright©2017 Tidewell Mamas.All Rights Reserved</div>

</body>
</html>
```